BWP Business Card

A double sided business card based on your "Brindlewood Partners Ltd" Logo. To use the "BWP" logo on 1 side and the full company logo on the reverse.

Detials to be included:

Name: Tomas Wheeler
Postion: Consultant Orthotist & Expert Witness
T: +44 (0) 7700 938271
F: +44 (0) 7654 8820

```html
<!DOCTYPE html>
<html lang="en">
<head>
<meta charset="utf-8">
<title>Brindlewood Partners Ltd – Business Card</title>
<link rel="stylesheet" href="https://fonts.googleapis.com/css2?family=Tinos:wght@400;700&display=swap">
<style>
  :root {
    --navy: #0f3a6e;
    --grey: #9a9a9a;
    --rule: #b9b9b9;
    --paper: #ffffff;
    --backdrop: #e9e7e3;
    --ink-muted: #7d7d7d;
  }
  * { box-sizing: border-box; margin: 0; padding: 0; }
  html, body {
    width: 1200px; height: 720px; overflow: hidden;
    background: var(--backdrop);
  }
  .stage {
    width: 1200px; height: 720px;
    display: flex; align-items: center; justify-content: center; gap: 40px;
  }
  .card {
    position: relative;
    width: 540px; height: 310px;
    background: var(--paper);
    box-shadow: 0 2px 8px rgba(0,0,0,.12);
    overflow: hidden;
    font-family: "Tinos", "Times New Roman", serif;
  }

  /* ---------- details side ---------- */
  .brand {
    position: absolute; left: 96px; top: 24px;
    display: flex; align-items: center; gap: 16px;
  }
  .brand-square { width: 64px; height: 64px; background: var(--navy); flex: none; }
  .brand-divider { width: 1px; height: 74px; background: var(--rule); flex: none; }
  .brand-name {
    font-weight: 700;
    color: var(--navy);
    font-size: 22px; line-height: 1.1;
  }
  .brand-tagline {
    margin-top: 6px; padding-top: 3px;
    border-top: 1px solid var(--navy);
    font-size: 9px; letter-spacing: .8px; text-transform: uppercase;
    color: var(--navy);
  }
  .band-top {
    position: absolute; left: 0; right: 0; top: 120px; height: 30px;
    background: var(--navy);
    border-top: 3px solid var(--rule);
  }
  .person {
    position: absolute; left: 96px; top: 166px;
    font-size: 14px; color: var(--ink-muted);
  }
  .person-name { font-weight: 700; color: var(--navy); font-size: 16px; }
  .band-bottom {
    position: absolute; left: 0; right: 0; bottom: 0; height: 92px;
    background: var(--navy);
    display: flex; align-items: center;
    color: var(--paper); font-size: 13px;
  }
  .address {
    font-style: normal;
    width: 236px; text-align: right; padding-right: 14px; line-height: 1.5;
  }
  .contact-divider { width: 1px; height: 62px; background: rgba(255,255,255,.55); }
  .contacts { list-style: none; padding-left: 14px; line-height: 1.55; }
  .contacts li { display: flex; align-items: center; gap: 6px; }
  .contacts svg { width: 11px; height: 11px; fill: var(--paper); flex: none; }

  /* ---------- logo side ---------- */
  .mark {
    position: absolute; inset: 0;
    display: flex; align-items: center; justify-content: center; gap: 20px;
  }
  .mark-square { width: 60px; height: 60px; background: var(--navy); flex: none; }
  .mark-name {
    font-weight: 700; font-size: 56px;
    color: var(--navy); line-height: 1;
  }
</style>
</head>
<body>
<main class="stage">

  <section class="card card-details" aria-label="Business card, details side">
    <div class="brand">
      <div class="brand-square"></div>
      <div class="brand-divider"></div>
      <div>
        <div class="brand-name">Brindlewood<br>Partners Ltd</div>
        <div class="brand-tagline">Excellence in Medical Legal Reporting</div>
      </div>
    </div>
    <div class="band-top"></div>

    <p class="person"><span class="person-name">Tomas Wheeler,</span> Consultant Orthotist &amp; Expert Witness</p>

    <div class="band-bottom">
      <address class="address">18 Harrow Lane Kingsford<br>Surrey, KT9 4RW</address>
      <div class="contact-divider"></div>
      <ul class="contacts">
        <li><svg viewBox="0 0 12 12" aria-hidden="true"><path d="M2.5 1h2l1 2.6-1.3 1a6 6 0 0 0 3.2 3.2l1-1.3L11 7.5v2A1.5 1.5 0 0 1 9.5 11 8.5 8.5 0 0 1 1 2.5 1.5 1.5 0 0 1 2.5 1z"/></svg>+44 (0) 7700 938271</li>
        <li><svg viewBox="0 0 12 12" aria-hidden="true"><path d="M3 1h5v3H3zM1 5h10v5H9V8H3v2H1zM3.5 9h5v2h-5z"/></svg>+44 (0) 7654 8820</li>
        <li><svg viewBox="0 0 12 12" aria-hidden="true"><path d="M1 3h10v6H1zM1.6 3.4 6 6.6l4.4-3.2v1L6 7.6 1.6 4.4z" fill-rule="evenodd"/></svg>tomas@brindlewoodpartners.co.uk</li>
      </ul>
    </div>
  </section>

  <section class="card card-mark" aria-label="Business card, logo side">
    <div class="mark">
      <div class="mark-square"></div>
      <div class="mark-name">BWP</div>
    </div>
  </section>

</main>
</body>
</html>
```